Moxy Fen needs some awesome stationary

Do you have what it takes to get my brand? You either do or you don't, have a crack at a design and you my just win my business.

I don't want to waste your or my time, so put your creative genius on either a business card or envelope.

I however need a package of stationary that follows the same brand. I will message you to complete the remaining should I like your first submission.

Here is what I need, have a go!

Basically I need the following for my small business based in melbourne.
- Letterhead (printer ready and MS Word)
- Business Card
- Compliments Slip
- Envelope
- Proposal Cover Page (MS Word only)
- Presentation Folder
- Marbled Fox Cards
- Student Name Tent
- Index Cards
- Vell-Ka

I am establishing the brand and it must be modern, professional but also relaxed; that is not formal and not corporate. It represents a company are leaders, but small enough to care and operate like a bunch of friends. We are bringing people and conversations back to business, and turfing out all the bureaucracy and crazy and wasteful procedures. Its about "lets talk and figure it out together and find even better ways".

Target Market(s)

Mainly companies that build software products, but Agile practices are used in many other industries (even graphic design projects)

Industry/Entity Type

Information Technology

Font styles to use
Sans Serif

Colors
3176b5
aaaaaa

Requirements
Must have
• I like curves and circles and not boxes or rectangles.
• I want a colour rich design with my brand colours, but it must be balanced.
• I want more modern than traditional, but simple modern
Should not have
• Not corporate
• Please don't waste my time if your not going to think about it.
• Don't mess with my primary logo
• Don't change my colours
• Don't overlay logo on image

```html
<!DOCTYPE html>
<html lang="en">
<head>
<meta charset="utf-8">
<title>Moxy Fen – Business Card</title>
<link rel="stylesheet" href="https://fonts.googleapis.com/css2?family=Open+Sans:wght@400;600;700&display=swap">
<style>
  :root {
    --page-bg: #e6e7ea;
    --card-face: #eef0f3;
    --blue-deep: #13226b;
    --blue-mid: #2a4aa8;
    --blue-brand: #3176b5;
    --swoosh-grey: #8e939f;
    --swoosh-light: #c3c6cd;
    --logo-navy: #26336a;
    --text-light: #f2f4fa;
    --text-soft: #d9def0;
  }
  * { margin: 0; padding: 0; box-sizing: border-box; }
  html, body {
    width: 1200px;
    height: 969px;
    overflow: hidden;
    background: var(--page-bg);
    font-family: "Open Sans", Arial, sans-serif;
  }
  .business-card {
    position: absolute;
    left: 100px;
    top: 200px;
    width: 1000px;
    height: 570px;
    border-radius: 6px;
    overflow: hidden;
    background: var(--card-face);
    box-shadow: 0 10px 30px rgba(0,0,0,0.18);
  }
  .card-shapes {
    position: absolute;
    inset: 0;
    width: 1000px;
    height: 570px;
  }
  .contact-block {
    position: absolute;
    left: 52px;
    top: 88px;
    color: var(--text-light);
  }
  .person-name {
    font-size: 34px;
    font-weight: 600;
    letter-spacing: 1px;
    line-height: 1;
  }
  .person-role {
    margin-top: 12px;
    font-size: 25px;
    line-height: 36px;
    color: var(--text-soft);
  }
  .postal-address {
    margin-top: 26px;
    font-size: 25px;
    line-height: 36px;
    color: var(--text-soft);
    font-style: normal;
  }
  .contact-list {
    list-style: none;
    margin-top: 24px;
  }
  .contact-list li {
    display: flex;
    align-items: center;
    height: 38.5px;
    font-size: 23px;
    color: var(--text-soft);
  }
  .contact-icon {
    width: 22px;
    height: 22px;
    margin-right: 14px;
    fill: var(--text-soft);
  }
  .brand-lockup {
    position: absolute;
    left: 600px;
    top: 300px;
    display: flex;
    align-items: center;
    gap: 20px;
  }
  .brand-dot {
    width: 54px;
    height: 54px;
    border-radius: 50%;
    background: var(--logo-navy);
  }
  .brand-name {
    font-size: 62px;
    font-weight: 700;
    color: var(--logo-navy);
    line-height: 1;
  }
</style>
</head>
<body>
  <div class="business-card">
    <svg class="card-shapes" viewBox="0 0 1000 570" aria-hidden="true">
      <defs>
        <linearGradient id="blue-panel" x1="0" y1="0" x2="1" y2="0.4">
          <stop offset="0" stop-color="var(--blue-mid)"/>
          <stop offset="0.55" stop-color="var(--blue-deep)"/>
          <stop offset="1" stop-color="#0e1a55"/>
        </linearGradient>
        <linearGradient id="grey-swoosh" x1="0" y1="0" x2="0" y2="1">
          <stop offset="0" stop-color="var(--swoosh-light)"/>
          <stop offset="1" stop-color="var(--swoosh-grey)"/>
        </linearGradient>
        <radialGradient id="face-glow" cx="0.75" cy="0.4" r="0.6">
          <stop offset="0" stop-color="#ffffff"/>
          <stop offset="1" stop-color="#e3e6ec"/>
        </radialGradient>
      </defs>
      <rect class="card-face" width="1000" height="570" fill="url(#face-glow)"/>
      <path class="blue-panel" d="M0 0 H585 C470 120 440 320 590 570 H0 Z" fill="url(#blue-panel)"/>
      <path class="grey-swoosh" d="M590 570 C490 420 462 300 488 185 C448 310 462 450 530 570 Z" fill="url(#grey-swoosh)"/>
    </svg>

    <div class="contact-block">
      <h1 class="person-name">DARA QUELL</h1>
      <p class="person-role">CEO<br>Professional Agile Trainer</p>
      <address class="postal-address">PO Box 4417<br>Harwick Vale<br>VIC 3990, Australia</address>
      <ul class="contact-list">
        <li>
          <svg class="contact-icon" viewBox="0 0 24 24"><path d="M6.6 10.8c1.4 2.8 3.8 5.1 6.6 6.6l2.2-2.2c.3-.3.7-.4 1-.2 1.1.4 2.3.6 3.6.6.6 0 1 .4 1 1V20c0 .6-.4 1-1 1C10.6 21 3 13.4 3 4c0-.6.4-1 1-1h3.5c.6 0 1 .4 1 1 0 1.3.2 2.5.6 3.6.1.3 0 .7-.2 1z"/></svg>
          1300MOXYFN
        </li>
        <li>
          <svg class="contact-icon" viewBox="0 0 24 24"><path d="M7 1h10c1.1 0 2 .9 2 2v18c0 1.1-.9 2-2 2H7c-1.1 0-2-.9-2-2V3c0-1.1.9-2 2-2zm0 3v14h10V4H7zm5 15.5a1.2 1.2 0 1 0 0 2.4 1.2 1.2 0 0 0 0-2.4z"/></svg>
          +61 400 172 386
        </li>
        <li>
          <svg class="contact-icon" viewBox="0 0 24 24"><path d="M2 5h20v14H2V5zm2 2v.5l8 5 8-5V7H4zm0 2.8V17h16V9.8l-8 5-8-5z"/></svg>
          dara@moxyfen.example
        </li>
        <li>
          <svg class="contact-icon" viewBox="0 0 24 24"><path d="M12 2a10 10 0 1 0 0 20 10 10 0 0 0 0-20zm-1 17.9A8 8 0 0 1 4.1 10L9 15v1c0 1.1.9 2 2 2v1.9zm6.9-2.5c-.3-.8-1-1.4-1.9-1.4h-1v-3c0-.6-.4-1-1-1H8v-2h2c.6 0 1-.4 1-1V7h2c1.1 0 2-.9 2-2v-.4a8 8 0 0 1 2.9 12.8z"/></svg>
          www.moxyfen.example
        </li>
      </ul>
    </div>

    <div class="brand-lockup">
      <span class="brand-dot"></span>
      <span class="brand-name">Moxy Fen</span>
    </div>
  </div>
</body>
</html>
```